Business cards to launch an education platform

Hi,
I am looking at having new business cards designed.
I am a startup, developing a web platform for schools and university, the education world. It's an online assessment system.
I would like a card that looks classy, and that is using the colors and the font of my logo.

I have attached:
1) my logo
2) A business card that I have designed quickly so you can have all the information required in the card, but I really don't like it.
3) The font that I am using (Lato Regular) to design my web platform
4) Some screenshots of my web platform so you can have a look at the style that I have.

Target Market(s)

Major market: Education system: Schools and university
Minor markets: Business in general

Industry/Entity Type

Business

Contact Information for Business Card

Clara Fenwick
Director

M: 0437 518 902
E: clara.fenwick@amberLoomSystems.com.au

Requirements
Must have
• The colors of my logo

```html
<!DOCTYPE html>
<html lang="en">
<head>
<meta charset="utf-8">
<title>Amber Loom systems — Business Card</title>
<link rel="stylesheet" href="https://fonts.googleapis.com/css2?family=Lato:wght@400;700&display=swap">
<style>
  :root {
    --stage: #000000;
    --card-front: #f2f2f2;
    --navy: #0d3a66;
    --name-blue: #1d4f91;
    --ink: #111111;
    --icon-blue: #1d5fa8;
    --cyan-core: #0fe2f2;
    --cyan-edge: #24acdf;
    --white: #ffffff;
  }
  * { margin: 0; padding: 0; box-sizing: border-box; }
  html, body {
    width: 1200px;
    height: 900px;
    overflow: hidden;
    background: var(--stage);
    font-family: "Lato", Arial, sans-serif;
  }
  .stage {
    position: relative;
    width: 1200px;
    height: 900px;
  }
  .card {
    position: absolute;
    top: 200px;
    width: 310px;
    height: 502px;
    overflow: hidden;
  }
  .card--front {
    left: 265px;
    background: var(--card-front);
    border-radius: 66px 0 66px 0;
  }
  .card--back {
    left: 641px;
    width: 309px;
    border-radius: 0 66px 0 66px;
    background: radial-gradient(circle at 50% 52%, var(--cyan-core) 0%, #18c8ea 35%, var(--cyan-edge) 100%);
  }
  .brand-mark {
    position: absolute;
    left: 144px;
    top: 62px;
    width: 56px;
    height: 56px;
    background: var(--navy);
  }
  .brand-name {
    position: absolute;
    right: 29px;
    top: 160px;
    text-align: right;
    color: var(--navy);
    font-weight: 400;
  }
  .brand-name__line1 {
    display: block;
    font-size: 34px;
    letter-spacing: 3px;
    line-height: 38px;
  }
  .brand-name__line2 {
    display: block;
    font-size: 22px;
    letter-spacing: 2.6px;
    line-height: 28px;
  }
  .person {
    position: absolute;
    left: 9px;
    top: 327px;
  }
  .person__name {
    font-size: 20px;
    color: var(--name-blue);
    line-height: 24px;
  }
  .person__title {
    font-size: 13px;
    color: var(--ink);
    line-height: 15px;
  }
  .contact {
    position: absolute;
    left: 9px;
    top: 395px;
    list-style: none;
  }
  .contact__item {
    display: flex;
    align-items: center;
    font-size: 14px;
    color: var(--ink);
    line-height: 21px;
    white-space: nowrap;
  }
  .contact__icon {
    width: 11px;
    height: 11px;
    margin-right: 6px;
    fill: var(--icon-blue);
  }
  .back-name {
    position: absolute;
    left: 0;
    right: 0;
    top: 214px;
    text-align: center;
    color: var(--white);
    font-weight: 400;
  }
  .back-name__line1 {
    display: block;
    font-size: 38px;
    letter-spacing: 3.4px;
    line-height: 40px;
  }
  .back-name__line2 {
    display: block;
    font-size: 24px;
    letter-spacing: 2.8px;
    line-height: 30px;
  }
</style>
</head>
<body>
<main class="stage">
  <section class="card card--front">
    <div class="brand-mark" aria-hidden="true"></div>
    <h1 class="brand-name">
      <span class="brand-name__line1">AMBER LOOM</span>
      <span class="brand-name__line2">systems</span>
    </h1>
    <div class="person">
      <p class="person__name">Clara Fenwick</p>
      <p class="person__title">Director</p>
    </div>
    <ul class="contact">
      <li class="contact__item">
        <svg class="contact__icon" viewBox="0 0 24 24" aria-hidden="true"><path d="M6.6 10.8a15.1 15.1 0 0 0 6.6 6.6l2.2-2.2a1 1 0 0 1 1-.25 11.4 11.4 0 0 0 3.6.57 1 1 0 0 1 1 1V20a1 1 0 0 1-1 1A17 17 0 0 1 3 4a1 1 0 0 1 1-1h3.5a1 1 0 0 1 1 1c0 1.25.2 2.45.57 3.57a1 1 0 0 1-.25 1z"/></svg>
        0437 518 902
      </li>
      <li class="contact__item">
        <svg class="contact__icon" viewBox="0 0 24 24" aria-hidden="true"><path d="M2 5h20v14H2z M2 5l10 8 10-8" fill="var(--icon-blue)"/><path d="M3 6l9 7 9-7" fill="none" stroke="#f2f2f2" stroke-width="1.6"/></svg>
        clara.fenwick@amberLoomSystems.com.au
      </li>
    </ul>
  </section>

  <section class="card card--back">
    <h2 class="back-name">
      <span class="back-name__line1">AMBER LOOM</span>
      <span class="back-name__line2">systems</span>
    </h2>
  </section>
</main>
</body>
</html>
```